Tovimar Community Development Planning New web site

Design a new web site. I have a budget of $1,500.00.
Attached on PowerPoint is a complete site plan. Home page and linked pages.
10 - 12 pages. All copy and photos will be supplied. (300dpi)
I have shown them the concept which they like.
No data bases required. Home page with animations dissolving.
They former web site has been taken down. They have been in business 30 years in New Jersey
Colors teal blues and greens
There will be a new logo)being designed)
The text in home page copy will give you a detailed story what they are all about.

files have been approved for Tovimar, Inc.   Brenton is the designer

```html
<!DOCTYPE html>
<html lang="en">
<head>
<meta charset="utf-8">
<title>Tovimar Inc. — Community Development Planning</title>
<link rel="stylesheet" href="https://fonts.googleapis.com/css2?family=Varela+Round&family=Open+Sans:wght@400&display=swap">
<style>
  :root {
    --brand-blue: #5a9bd2;
    --text-grey: #4f5155;
    --cta-yellow: #f1bf00;
    --cta-text: #3a3a3a;
    --nav-green: #4ca114;
    --nav-divider: #3f8c0e;
    --nav-text: #ffffff;
    --nav-active: #f0c64a;
    --nav-muted: #92cc6c;
    --hero-light: #fbfbfb;
    --hero-mid: #e9ebea;
    --slider-arrow: #6f6f6f;
    --dot-idle: #cfcfcf;
    --dot-active: #111111;
  }
  * { box-sizing: border-box; margin: 0; padding: 0; }
  html, body { width: 1200px; height: 615px; overflow: hidden; background: var(--hero-light); }
  .page { position: relative; width: 1200px; height: 615px; overflow: hidden; font-family: "Open Sans", sans-serif; }

  .hero-backdrop {
    position: absolute; inset: 0 0 52px 0;
    background:
      radial-gradient(ellipse 420px 260px at 640px 200px, rgba(200,196,190,0.45), transparent 70%),
      radial-gradient(ellipse 380px 240px at 1000px 420px, rgba(210,214,214,0.5), transparent 70%),
      linear-gradient(90deg, var(--hero-light) 0%, #f3f3f2 45%, var(--hero-mid) 100%);
  }

  .brand {
    position: absolute; left: 126px; top: 46px;
    font-family: "Varela Round", sans-serif; font-size: 40px;
    color: var(--brand-blue); letter-spacing: 0.5px;
  }

  .slide-title {
    position: absolute; left: 124px; top: 186px;
    font-family: "Varela Round", sans-serif; font-weight: 400;
    font-size: 38px; line-height: 38px; color: var(--brand-blue);
  }
  .slide-text {
    position: absolute; left: 126px; top: 273px; width: 380px;
    font-size: 17.5px; line-height: 19.5px; color: var(--text-grey);
  }
  .cta {
    position: absolute; left: 126px; top: 336px; width: 166px; height: 38px;
  }
  .cta svg { position: absolute; inset: 0; }
  .cta span {
    position: absolute; left: 26px; top: 0; line-height: 38px;
    font-family: "Varela Round", sans-serif; font-size: 17.5px; color: var(--cta-text);
  }

  .slide-dots { position: absolute; left: 127px; top: 437px; display: flex; gap: 2.5px; }
  .slide-dots i { width: 13px; height: 13px; border-radius: 50%; background: var(--dot-idle); display: block; }
  .slide-dots i.is-active { background: var(--dot-active); }

  .slider-arrow { position: absolute; top: 238px; width: 58px; height: 58px; }
  .slider-arrow--prev { left: -24px; }
  .slider-arrow--next { left: 1167px; }

  .slide-visual {
    position: absolute; left: 588px; top: 116px; width: 486px; height: 410px;
    border-radius: 10px;
    background: linear-gradient(180deg, #3b3f3a 0%, #5d7a4a 22%, #9fb3b8 55%, #dfe3e3 85%, #eeeeee 100%);
  }

  .main-nav {
    position: absolute; left: 0; top: 563px; width: 1200px; height: 52px;
    background: var(--nav-green); display: flex; align-items: stretch;
    padding-left: 118px;
    font-family: "Varela Round", sans-serif; font-size: 17.5px;
  }
  .main-nav a {
    color: var(--nav-text); text-decoration: none;
    display: flex; align-items: center; padding: 0 9px;
    border-right: 1px solid var(--nav-divider);
  }
  .main-nav a:last-of-type { border-right: none; }
  .main-nav a.is-current { color: var(--nav-active); }
  .copyright {
    position: absolute; right: 126px; top: 0; line-height: 52px;
    font-family: "Open Sans", sans-serif; font-size: 17.5px; color: var(--nav-muted);
  }
</style>
</head>
<body>
<div class="page">
  <div class="hero-backdrop" role="img" aria-label="Soft blurred photo of hands reviewing architectural plans with a pencil"></div>

  <div class="brand">Tovimar Inc.</div>

  <h1 class="slide-title">Conduct<br>Placement Lotteries</h1>
  <p class="slide-text">Explain implementation of a lottery and select applicants and keep you out of that process</p>

  <div class="cta">
    <svg width="166" height="38" viewBox="0 0 166 38">
      <polygon points="0,0 150,0 140,19 150,38 0,38" fill="var(--cta-yellow)" transform="translate(0,0)"/>
      <polygon points="150,0 166,19 150,38 140,19" fill="var(--cta-yellow)" transform="translate(0,0)" opacity="0"/>
    </svg>
    <span>Call to Action</span>
  </div>

  <div class="slide-dots"><i class="is-active"></i><i></i><i></i></div>

  <svg class="slider-arrow slider-arrow--prev" viewBox="0 0 58 58">
    <circle cx="29" cy="29" r="29" fill="var(--slider-arrow)" opacity="0.85"/>
    <polyline points="38,20 30,29 38,38" fill="none" stroke="#ffffff" stroke-width="3"/>
  </svg>
  <svg class="slider-arrow slider-arrow--next" viewBox="0 0 58 58">
    <circle cx="29" cy="29" r="29" fill="var(--slider-arrow)" opacity="0.85"/>
    <polyline points="17,20 25,29 17,38" fill="none" stroke="#ffffff" stroke-width="3"/>
  </svg>

  <div class="slide-visual" role="img" aria-label="Desktop monitor showing the new website home page with a team photo"></div>

  <nav class="main-nav">
    <a href="#">Home</a>
    <a href="#" class="is-current">Company</a>
    <a href="#">Services</a>
    <a href="#">Housing Rehab Application</a>
    <a href="#">Affordable Application</a>
    <a href="#">Contact</a>
    <span class="copyright">©2014</span>
  </nav>
</div>
</body>
</html>
```